Companybrochure for Consulting & Financing Firm

I need to have a Company Brochure asap for our company. We have a website that describes what we do, but we need also a brochure, that can be sent by PDF of eventually be printed as well.

The brochure should be short but nice and appealing to the customers.

We provide professional management consulting and help our customers to get finance for very diferent projects. Our business has a lot to do with personal relations, but also we are very professional in the way we work and how develop the solutions for our clients. Our clients are mainly government-owned firm, but also private trading companies and wealthy private investors.

Our customers are mainly in Latin America, but the company is headquater is in Switzerland. We are opening offices in Panama and Caracas, this should be easaly be adabtable later.

Please have a look at our website www.vorelpartners.ch. In the brochure, we would segment our services in 1.) Project Developments 2.) Management Conulting 3.) Investment Management and 4.) Finance Solutions.

Also do have a look at www.vorelpartners.ch
(Click E for the English version)
Updates

I managed to put the Mock-Up to the Website.
It is actually not really a mock-up, it is a version I have designed myself.
Well as I am not a designer, I hope you can make it much better.
The content however is what I would put in any other design as well.

Target Market(s)

Top Management, Investors, Entrepreneurs, Government Officials

Industry/Entity Type

Management Consulting

Requirements
Must have
• Design should reflect this image elements:

We are entrepreneurs.
We are comitted to get things done.
We work closely with the client side by side.
We are a professional partner.
We are not afraid of delivering unconventional solutions.
We look at the problem from various angles.
We analyse, develop solutions and implent results.
Should not have
• Typical US-American style elements. We do not want to give the impression of being a US company.

We do not want to appear to be neo-liberal. We are a politically neutral professional consulting firm.

```html
<!DOCTYPE html>
<html lang="en">
<head>
<meta charset="utf-8">
<title>Vorel Partners AG – Investment Management</title>
<link href="https://fonts.googleapis.com/css2?family=Roboto:wght@300;400;500;700&display=swap" rel="stylesheet">
<style>
  :root {
    --ink: #1c1c1c;
    --text: #222222;
    --brand-green: #6c9a2b;
    --panel-green: #76a032;
    --band-dark: #0e0e0e;
    --sheet: #ffffff;
    --sheet-border: #d4d4d4;
    --white: #ffffff;
  }
  * { margin: 0; padding: 0; box-sizing: border-box; }
  html, body {
    width: 1200px;
    height: 953px;
    overflow: hidden;
    background: var(--white);
    font-family: "Roboto", Arial, sans-serif;
  }
  .canvas { position: relative; width: 1200px; height: 953px; }

  .sheet {
    position: absolute;
    left: 36px; top: 33px;
    width: 1135px; height: 795px;
    background: var(--sheet);
    border: 1px solid var(--sheet-border);
    box-shadow: 0 0 24px rgba(0,0,0,0.12);
  }
  .rule-top {
    position: absolute; left: 0; top: 45px;
    width: 100%; height: 11px;
    background: var(--ink);
  }
  .brand-name {
    position: absolute; right: 32px; top: 96px;
    font-size: 42px; font-weight: 700;
    color: #2d2d2d; letter-spacing: -0.01em;
    line-height: 1;
  }

  .hero {
    position: absolute; left: 0; top: 167px;
    width: 100%; height: 254px;
    overflow: hidden;
  }
  .hero-visual { position: absolute; inset: 0; width: 100%; height: 100%; }
  .hero-title {
    position: absolute; left: 30px; top: 112px;
    color: var(--white);
    font-size: 78px; line-height: 0.74;
    letter-spacing: -0.065em;
    text-transform: uppercase;
  }
  .hero-title .light { display: block; font-weight: 300; }
  .hero-title .bold { display: block; font-weight: 700; }

  .intro {
    position: absolute; left: 29px; top: 452px;
    width: 570px;
    color: var(--text);
  }
  .intro-lead {
    color: var(--brand-green);
    font-size: 19.5px; font-weight: 700;
    line-height: 22px; margin-bottom: 20px;
  }
  .intro p {
    font-size: 16.8px; font-weight: 700;
    line-height: 21.8px; margin-bottom: 21.8px;
  }

  .testimonials {
    position: absolute; left: 692px; top: 449px;
    width: 411px;
  }
  .testimonials-title {
    position: relative;
    height: 41px;
    background: var(--ink);
    color: var(--white);
    font-size: 16.5px; font-weight: 500;
    line-height: 41px; text-align: center;
  }
  .testimonials-title::before {
    content: ""; position: absolute; left: 0; top: 0;
    border-top: 19px solid var(--panel-green);
    border-right: 26px solid transparent;
  }
  .testimonials-body {
    background: var(--panel-green);
    color: var(--white);
    font-size: 13.9px; font-weight: 300;
    line-height: 22px; text-align: justify;
    padding: 19px 13px 12px;
    height: 250px;
  }

  .rule-bottom {
    position: absolute; left: 36px; top: 940px;
    width: 1135px; height: 10px;
    background: var(--ink);
  }
</style>
</head>
<body>
<div class="canvas">
  <div class="sheet">
    <div class="rule-top"></div>
    <div class="brand-name">Vorel Partners AG</div>

    <div class="hero">
      <svg class="hero-visual" viewBox="0 0 1135 254" preserveAspectRatio="none" role="img" aria-label="Mountain landscape with soaring birds behind diagonal green and black bands">
        <defs>
          <linearGradient id="sky" x1="0" y1="0" x2="0" y2="1">
            <stop offset="0" stop-color="#6a6a6a"/>
            <stop offset="0.6" stop-color="#a3a3a3"/>
            <stop offset="0.8" stop-color="#3a3a3a"/>
            <stop offset="1" stop-color="#111111"/>
          </linearGradient>
          <linearGradient id="greenBand" x1="0" y1="0" x2="0" y2="1">
            <stop offset="0" stop-color="#2f6b12"/>
            <stop offset="1" stop-color="#0f2a05"/>
          </linearGradient>
        </defs>
        <rect width="1135" height="254" fill="url(#sky)"/>
        <polygon points="0,0 155,0 0,254" fill="#8a8a8a"/>
        <polygon points="155,0 645,0 495,254 0,254" fill="var(--band-dark)"/>
        <polygon points="645,0 735,0 580,254 495,254" fill="url(#greenBand)"/>
        <polygon points="990,0 1135,0 1135,254 845,254" fill="url(#greenBand)"/>
        <rect x="0" y="215" width="1135" height="39" fill="#0a0a0a" opacity="0.7"/>
      </svg>
      <h1 class="hero-title"><span class="light">Investment</span><span class="bold">Management</span></h1>
    </div>

    <section class="intro">
      <h2 class="intro-lead">Vorel Partners has a clear business-like<br>approach to investments.</h2>
      <p>We only engage in those projects or companies with which we have a strong relationship.</p>
      <p>That is why we are also willing to take an entrepreneurial risk in the companies we invest in. We participate with our own capital and assume functions in the company's management.</p>
      <p>Vorel Partners currently holds shares in seven SMEs; four of these to 100%. Participation is on equal terms, and two of of the companies we are minority shareholders.</p>
    </section>

    <aside class="testimonials">
      <h3 class="testimonials-title">WHAT OUR CLIENTS HAVE TO SAY...</h3>
      <div class="testimonials-body">Lorem Ipsum is simply dummy text of the printing and typesetting industry. Lorem Ipsum has been the industry's standard dummy text ever since the 1500s, when an unknown printer took a galley of type and scrambled it to make a type specimen book. It has survived not only five centuries, but also the leap into electronic typesetting, remaining essentially unchanged. It was popularised in the 1960s with the release of Letraset sheets containing Lorem Ipsum passages, and more recently with desktop publishing software like</div>
    </aside>
  </div>
  <div class="rule-bottom"></div>
</div>
</body>
</html>
```